Health Care Company with Logo Needs Business Cards designed

We are a luxury behavioral health company looking for business cards design we already have a logo and are looking for someone to design a sophisticated luxurious looking business card. Please note that Card design should be captivating just like the logo and also encompass the logo color

Industry/Entity Type

Healthcare

Contact Information for Business Card

Logo,company name, tagline, my name and title, contact details, and physical address

```html
<!DOCTYPE html>
<html lang="en">
<head>
<meta charset="utf-8">
<title>Corvin Behavioral Health — Business Cards</title>
<link rel="stylesheet" href="https://fonts.googleapis.com/css2?family=Roboto:wght@400;700;900&display=swap">
<style>
  :root {
    --bg: #e9e9ea;
    --paper: #ffffff;
    --purple: #6a2c8e;
    --purple-dark: #4e1d6c;
    --purple-light: #8c45b4;
    --blue: #1ea0dc;
    --orange: #ef8a1e;
    --green: #6fae34;
    --ink: #4a4a4a;
    --rule: #5a5a5a;
    --silver: #e4e4ea;
  }
  * { margin: 0; padding: 0; box-sizing: border-box; }
  html, body { width: 1200px; height: 802px; overflow: hidden; }
  body {
    background: var(--bg);
    font-family: "Roboto", Arial, sans-serif;
    position: relative;
  }
  .card {
    position: absolute;
    width: 540px;
    height: 309px;
    top: 246px;
    overflow: hidden;
    box-shadow: 0 6px 18px rgba(0,0,0,0.12);
  }
  .card-front { left: 40px; background: var(--paper); }
  .card-back {
    left: 620px;
    background: linear-gradient(135deg, var(--purple-light) 0%, var(--purple) 45%, var(--purple-dark) 100%);
  }

  /* front */
  .brand {
    position: absolute;
    left: 150px;
    top: 50px;
    display: flex;
    align-items: center;
    gap: 12px;
  }
  .brand-square { width: 30px; height: 30px; background: var(--purple); }
  .brand-name {
    font-weight: 900;
    font-size: 24px;
    color: var(--purple);
    line-height: 1;
  }
  .brand-tagline {
    font-size: 7.5px;
    font-weight: 700;
    letter-spacing: 1.6px;
    text-transform: uppercase;
    color: var(--blue);
    margin-top: 4px;
  }
  .divider {
    position: absolute;
    left: 36px;
    right: 36px;
    top: 178px;
    height: 1px;
    background: var(--rule);
  }
  .person { position: absolute; left: 36px; top: 124px; }
  .person-name { font-size: 24px; font-weight: 700; color: var(--blue); line-height: 1.1; }
  .person-title { font-size: 15px; color: var(--ink); margin-top: 3px; }
  .contacts {
    position: absolute;
    left: 36px;
    top: 192px;
    list-style: none;
    font-size: 15px;
    color: var(--ink);
  }
  .contacts li { display: flex; align-items: center; gap: 10px; line-height: 23px; }
  .contacts svg { width: 13px; height: 13px; flex: none; }
  .address {
    position: absolute;
    right: 36px;
    top: 128px;
    text-align: right;
    font-size: 15px;
    color: var(--ink);
    line-height: 1.3;
  }
  .color-band {
    position: absolute;
    left: 0; right: 0; bottom: 0;
    height: 14px;
    display: flex;
  }
  .color-band span { flex: 1; }
  .color-band .purple { background: var(--purple); flex: 1.3; }
  .color-band .blue { background: var(--blue); }
  .color-band .orange { background: var(--orange); }
  .color-band .green { background: var(--green); flex: 0.7; }

  /* back */
  .back-brand { position: absolute; right: 30px; top: 48px; text-align: left; }
  .back-name { font-size: 30px; font-weight: 900; color: var(--silver); line-height: 1; }
  .back-tagline {
    font-size: 9px;
    font-weight: 700;
    letter-spacing: 2.3px;
    text-transform: uppercase;
    color: var(--blue);
    margin-top: 6px;
  }
</style>
</head>
<body>
  <section class="card card-front" aria-label="Business card front">
    <div class="brand">
      <div class="brand-square"></div>
      <div>
        <div class="brand-name">Corvin Behavioral Health</div>
        <div class="brand-tagline">Dedicated to hope, healing and recovery</div>
      </div>
    </div>

    <div class="person">
      <div class="person-name">Daniel Hart</div>
      <div class="person-title">Manager</div>
    </div>

    <div class="address">Your address, city<br>state, ZIP 0000</div>

    <div class="divider"></div>

    <ul class="contacts">
      <li>
        <svg viewBox="0 0 24 24" fill="var(--blue)"><path d="M6.6 10.8a15.1 15.1 0 0 0 6.6 6.6l2.2-2.2a1 1 0 0 1 1-.25 11.4 11.4 0 0 0 3.6.57 1 1 0 0 1 1 1V20a1 1 0 0 1-1 1A17 17 0 0 1 3 4a1 1 0 0 1 1-1h3.5a1 1 0 0 1 1 1c0 1.25.2 2.45.57 3.57a1 1 0 0 1-.25 1z"/></svg>
        555-014-2290
      </li>
      <li>
        <svg viewBox="0 0 24 24" fill="none" stroke="var(--blue)" stroke-width="2.2"><rect x="3" y="5" width="18" height="14" rx="1"/><path d="M3 6l9 7 9-7"/></svg>
        hello@corvinmail.com
      </li>
      <li>
        <svg viewBox="0 0 24 24" fill="none" stroke="var(--blue)" stroke-width="2"><circle cx="12" cy="12" r="9"/><path d="M3 12h18M12 3c3 3 3 15 0 18M12 3c-3 3-3 15 0 18"/></svg>
        www.corvinhealth.com
      </li>
    </ul>

    <div class="color-band">
      <span class="purple"></span><span class="blue"></span><span class="orange"></span><span class="green"></span>
    </div>
  </section>

  <section class="card card-back" aria-label="Business card back">
    <div class="back-brand">
      <div class="back-name">Corvin Behavioral Health</div>
      <div class="back-tagline">Dedicated to hope, healing and recovery</div>
    </div>
  </section>
</body>
</html>
```